UI/ UX Design for ERP Software

We need a new UX/UI interface for a ERP software for property managers. Our CMMS / ERP solution is made based on responsive design technologies and is coded in PHP.
The overall UX to be similar to Tev Ulna - easy navigation, intuitive menus.

Industry/Entity Type

Property Management

Number of Pages Required

5+ page

Requirements
Must have
• Round dock buttons
Consistent icons across the application
Enough Spacing between buttons/icons/ menu
Consistent Font
Nice to have
• We would like the UX to allow the users to use the application without /minimum training.
Should not have
• we don't want anything that is classic with respect to UX

```html
<!DOCTYPE html>
<html lang="en">
<head>
<meta charset="utf-8">
<title>Keyhold — Active Dashboard</title>
<link href="https://fonts.googleapis.com/css2?family=Questrial&display=swap" rel="stylesheet">
<style>
:root{
  --blue:#0a7cf5;
  --navy-top:#05060c;
  --navy-bottom:#0b1a3c;
  --card-head:#3a3a3c;
  --chip:#a9abb0;
  --ink:#1d1f24;
  --grid:#c9cbd0;
  --page:#ffffff;
  --bar:#5fa8ff;
}
*{box-sizing:border-box;margin:0;padding:0}
html,body{width:1200px;height:724px;overflow:hidden;background:var(--page);font-family:"Questrial",sans-serif;color:var(--ink)}
.app{position:relative;width:1200px;height:724px}
.sidebar{position:absolute;left:0;top:0;width:213px;height:724px;background:linear-gradient(180deg,var(--navy-top) 0%,var(--navy-top) 25%,var(--navy-bottom) 100%)}
.brand{position:absolute;left:5px;top:6px;width:203px;height:63px;background:#fff;display:flex;align-items:center;justify-content:center;gap:8px}
.brand-mark{width:18px;height:18px;background:var(--blue);border-radius:3px}
.brand-name{font-size:26px;color:var(--blue)}
.menu{position:absolute;left:0;top:102px;width:198px;list-style:none}
.menu li{height:39px;border-bottom:1.5px solid #e8eaf0;display:flex;align-items:center;color:#fff;font-size:13px;gap:8px;padding-left:12px}
.menu svg{width:19px;height:19px;flex:none;stroke:#fff;fill:none;stroke-width:1.4}
.scroll{position:absolute;left:203px;top:108px;width:5px;height:590px;border-radius:3px;background:#1b2740}
.scroll i{position:absolute;left:0;top:0;width:5px;height:109px;border-radius:3px;background:var(--blue)}
.topbar{position:absolute;left:213px;top:0;width:987px;height:69px;background:var(--blue);color:#fff}
.title{position:absolute;left:16px;top:22px;display:flex;align-items:center;gap:10px;font-size:16px;letter-spacing:.2px}
.title svg{width:26px;height:24px;stroke:#fff;fill:none;stroke-width:2}
.stat{position:absolute;top:18px;height:34px;background:#fff;border-radius:3px;color:var(--ink);padding:2px 0 0 7px}
.stat .k{font-size:10px;color:#333;line-height:12px}
.stat .v{font-size:12.5px;line-height:16px;display:flex;align-items:center;gap:3px}
.stat .v svg{width:11px;height:11px;stroke:#333;fill:none;stroke-width:1.4}
.card{position:absolute;left:229px;top:97px;width:951px;height:513px;border-radius:9px;background:#fff;box-shadow:0 2px 8px rgba(0,0,0,.15);overflow:hidden}
.card-head{height:43px;background:var(--card-head);color:#fff;position:relative}
.range{position:absolute;left:12px;top:12px;display:flex;align-items:center;gap:8px;font-size:14px}
.range svg{width:20px;height:20px;stroke:#fff;fill:none;stroke-width:1.6}
.chip{position:absolute;top:8px;height:28px;border-radius:2px;background:var(--chip);color:#fff;font-size:10.5px;display:flex;align-items:center;gap:4px;padding-left:5px}
.chip.on{background:#fff;color:var(--ink)}
.chip svg{width:14px;height:14px;fill:none;stroke:currentColor;stroke-width:1.3}
.chart{position:absolute;left:0;top:43px}
.footer{position:absolute;left:598px;top:693px;width:200px;text-align:center;font-size:9.5px;color:#333}
.code{position:absolute;left:1153px;top:693px;font-size:9.5px;color:#333}
</style>
</head>
<body>
<div class="app">
  <aside class="sidebar">
    <div class="brand"><span class="brand-mark"></span><span class="brand-name">Keyhold</span></div>
    <ul class="menu">
      <li><svg viewBox="0 0 20 20"><path d="M2 15a8 8 0 1 1 16 0"/><path d="M10 15l4-5"/></svg>Dashboards</li>
      <li><svg viewBox="0 0 20 20"><rect x="2" y="6" width="16" height="11" rx="1"/><path d="M7 6V3h6v3M2 11h16"/></svg>Customers</li>
      <li><svg viewBox="0 0 20 20"><rect x="3" y="3" width="9" height="15"/><rect x="12" y="8" width="5" height="10"/><path d="M5 6h2M8 6h2M5 9h2M8 9h2M5 12h2M8 12h2"/></svg>Properties</li>
      <li><svg viewBox="0 0 20 20"><path d="M2 13l2-6h12l2 6v3H2z"/><path d="M2 13h16"/><circle cx="5" cy="16" r="1"/><circle cx="15" cy="16" r="1"/></svg>Tenants</li>
      <li><svg viewBox="0 0 20 20"><rect x="2" y="3" width="12" height="15"/><path d="M5 7h6M5 10h6M5 13h4M10 14l8-9"/></svg>Contacts</li>
      <li><svg viewBox="0 0 20 20"><circle cx="10" cy="10" r="3"/><circle cx="10" cy="10" r="7" stroke-dasharray="3 2"/></svg>Contractors</li>
      <li><svg viewBox="0 0 20 20"><circle cx="5" cy="5" r="2"/><circle cx="15" cy="5" r="2"/><path d="M2 12v-3h6v3M12 12v-3h6v3M4 18l2-5M16 18l-2-5"/></svg>Employees</li>
      <li><svg viewBox="0 0 20 20"><circle cx="10" cy="10" r="8"/><path d="M12 7H9a1.5 1.5 0 0 0 0 3h2a1.5 1.5 0 0 1 0 3H8M10 5v10"/></svg>Compliance Management</li>
      <li><svg viewBox="0 0 20 20"><path d="M1 8h18l-2 9H3z"/><path d="M6 8l4-5 4 5M7 11v4M10 11v4M13 11v4"/></svg>Prevent. Maintenance</li>
      <li><svg viewBox="0 0 20 20"><path d="M1 9l4-3 4 2 3-2 7 3-3 5-4 2-5-3z"/><path d="M9 8l4 4"/></svg>Work Orders</li>
      <li><svg viewBox="0 0 20 20"><rect x="4" y="4" width="12" height="11"/><path d="M1 18h18M7 8h6M7 11h6"/></svg>Purchase Orders</li>
      <li><svg viewBox="0 0 20 20"><rect x="1" y="2" width="15" height="14"/><path d="M4 13V9M7 13V6M10 13V8"/><circle cx="15" cy="14" r="3"/><path d="M17 16l2 2"/></svg>Property Inspections</li>
      <li><svg viewBox="0 0 20 20"><circle cx="10" cy="10" r="3"/><circle cx="10" cy="10" r="7"/><path d="M10 1v3M10 16v3M1 10h3M16 10h3"/></svg>Energy Management</li>
      <li><svg viewBox="0 0 20 20"><circle cx="10" cy="10" r="8"/><ellipse cx="10" cy="10" rx="3.5" ry="8"/><path d="M2 10h16M3.5 6h13M3.5 14h13"/></svg>Risk Management</li>
      <li><svg viewBox="0 0 20 20"><rect x="2" y="2" width="14" height="16"/><circle cx="10" cy="10" r="4"/><path d="M13 13l5 5"/></svg>Project Management</li>
    </ul>
    <div class="scroll"><i></i></div>
  </aside>

  <header class="topbar">
    <div class="title"><svg viewBox="0 0 26 24"><path d="M2 12L13 2l11 10M5 10v12h6v-7h4v7h6V10"/></svg>ACTIVE DASHBOARD</div>
    <div class="stat" style="left:492px;width:62px"><div class="k">Properties</div><div class="v"><svg viewBox="0 0 12 12"><path d="M1 6l5-5 5 5M2.5 5v6h7V5"/></svg>3</div></div>
    <div class="stat" style="left:560px;width:51px"><div class="k">Tenants</div><div class="v"><svg viewBox="0 0 12 12"><path d="M1 6l5-5 5 5M2.5 5v6h7V5"/></svg>8</div></div>
    <div class="stat" style="left:618px;width:111px"><div class="k">Total Properties Area</div><div class="v"><svg viewBox="0 0 12 12"><path d="M6 0v12M0 6h12"/></svg>422, 000.00sq.ft.</div></div>
    <div class="stat" style="left:734px;width:111px"><div class="k">Rented Area</div><div class="v"><svg viewBox="0 0 12 12"><path d="M6 0v12M0 6h12"/></svg>233, 500.00sq.ft.</div></div>
    <div class="stat" style="left:851px;width:111px"><div class="k">Vacancies Area</div><div class="v"><svg viewBox="0 0 12 12"><path d="M6 0v12M0 6h12"/></svg>188, 500.00sq.ft.</div></div>
  </header>

  <section class="card">
    <div class="card-head">
      <div class="range"><svg viewBox="0 0 20 20"><path d="M1 19h18M3 19V9h3v10M8 19V2h3v17M13 19v-6h3v6"/></svg>12/27/2020 - 01/03/2021</div>
      <div class="chip on" style="left:385px;width:82px"><svg viewBox="0 0 14 14"><circle cx="7" cy="7" r="6"/><path d="M7 3v4h3"/></svg>Last 7 days</div>
      <div class="chip" style="left:472px;width:85px"><svg viewBox="0 0 14 14"><circle cx="7" cy="7" r="6"/><path d="M7 3v4h3"/></svg>Last months</div>
      <div class="chip" style="left:562px;width:95px"><svg viewBox="0 0 14 14"><circle cx="7" cy="7" r="6"/><path d="M7 3v4h3"/></svg>Last 3 months</div>
      <div class="chip" style="left:661px;width:81px"><svg viewBox="0 0 14 14"><circle cx="7" cy="7" r="6"/><path d="M7 3v4h3"/></svg>Last 7 days</div>
      <div class="chip" style="left:747px;width:87px"><svg viewBox="0 0 14 14"><circle cx="7" cy="7" r="6"/><path d="M7 3v4h3"/></svg>Next months</div>
      <div class="chip" style="left:839px;width:98px"><svg viewBox="0 0 14 14"><circle cx="7" cy="7" r="6"/><path d="M7 3v4h3"/></svg>Next 3 months</div>
    </div>
    <svg class="chart" width="951" height="470" viewBox="0 0 951 470" font-family="Questrial, sans-serif" font-size="10.5" fill="#1d1f24">
      <g stroke="var(--grid)" stroke-width="1">
        <line x1="59" y1="43" x2="940" y2="43"/>
        <line x1="59" y1="81" x2="940" y2="81"/>
        <line x1="59" y1="119" x2="940" y2="119"/>
        <line x1="59" y1="157" x2="940" y2="157"/>
        <line x1="59" y1="195" x2="940" y2="195"/>
        <line x1="59" y1="233" x2="940" y2="233" stroke="#9a9ca2"/>
      </g>
      <g stroke="#9a9ca2">
        <line x1="59.5" y1="233" x2="59.5" y2="246"/><line x1="157" y1="233" x2="157" y2="246"/>
        <line x1="255" y1="233" x2="255" y2="246"/><line x1="352" y1="233" x2="352" y2="246"/>
        <line x1="450" y1="233" x2="450" y2="246"/><line x1="548" y1="233" x2="548" y2="246"/>
        <line x1="645" y1="233" x2="645" y2="246"/><line x1="743" y1="233" x2="743" y2="246"/>
        <line x1="840" y1="233" x2="840" y2="246"/>
      </g>
      <g text-anchor="end">
        <text x="51" y="47">1.25</text><text x="51" y="85">1</text><text x="51" y="123">0.75</text>
        <text x="51" y="161">0.5</text><text x="51" y="199">0.25</text><text x="51" y="237">0</text>
      </g>
      <text x="0" y="0" transform="translate(20 138) rotate(-90)" text-anchor="middle">Number</text>
      <g text-anchor="middle">
        <text x="108" y="260">12/27/2020</text><text x="206" y="260">12/28/2020</text>
        <text x="304" y="260">12/29/2020</text><text x="401" y="260">12/30/2020</text>
        <text x="499" y="260">12/31/2020</text><text x="596" y="260">01/01/2020</text>
        <text x="693" y="260">01/02/2020</text><text x="791" y="260">01/03/2020</text>
      </g>
      <rect x="364" y="60" width="6.5" height="151" fill="var(--bar)"/>
      <g font-size="11">
        <rect x="58" y="308" width="13" height="11" fill="#0a7cf5"/><text x="77" y="318">Scheduled Maintenance</text>
        <rect x="58" y="327" width="13" height="11" fill="#8fe37f"/><text x="77" y="337">Completed Scheduled Maintenance</text>
        <rect x="58" y="347" width="13" height="11" fill="#f6a55e"/><text x="77" y="357">Future Scheduled Maintenance</text>
        <rect x="58" y="366" width="13" height="11" fill="#424148"/><text x="77" y="376">Scheduled Work Orders</text>
        <rect x="58" y="386" width="13" height="11" fill="#8688ec"/><text x="77" y="396">Completed Work Orders</text>
        <rect x="58" y="405" width="13" height="11" fill="#ef5d80"/><text x="77" y="415">Property Inspections In Progress</text>
        <rect x="58" y="425" width="13" height="11" fill="#e6d352"/><text x="77" y="435">Completed Property Inspections</text>
      </g>
    </svg>
  </section>

  <div class="footer">COPYRIGHTS @ 2021 KEYHOLD.</div>
  <div class="code">C20</div>
</div>
</body>
</html>
```